2018 Desk Calendar Design with Better Spine, Better Health with Chiropractic

In conjunction with the Federation of Spinal Wellness Malaysia (FSW), we are organizing a 2018 desk calendar design. The cover page and monthly design size is 210mm (H) x 195mm (W). The will be a total of 27 designs including a cover page (front) [Sample 1], cover page (back) Malaysia National & States Holiday 2018 (https://restdaylist.example.my/2018-dates/) [Sample 2], 12 months design (front) [Sample 3 and 4], 12 months design (back) [Sample 5], Last page (2017 and 2019 calendar) [Sample 6].

Below are some recommendations for monthly back cover design. The main theme remain as Better SPINE, Better HEALTH with CHIROPRACTIC. Each month can in collaborate with of the following element:-

Suggestion 1 (Celebration of the Month)
January - New Year
February - Chinese New Year
March -
April -
May - Labour Day
June - Aidilfitri Festival
July-
August - Independent Day
September - Malaysia Day
October - World Spine Day
November - Deepavali Festival
December - Christmas

Suggestion 2 (States in Malaysia)
January - Perlis
February - Kedah
March - Penang
April - Perak
May - Selangor
June - Negeri Sembilan
July- Melaka
August - Johor
September - Pahang
October - Terengganu
November - Kelantan
December - Sabah & Sarawak

Target Market(s)

Chiropractors and Public

Industry/Entity Type

Chiropractor

Colors

Designer to choose colors to be used in the design.

Requirements
Must have
• The theme for the desk calendar design is Better Spine, Better Health with Chiropractic.
• The cover page should include 5th Anniversary element.
Nice to have
• Lunar or Islamic calendar is optional in the Gregorian calendar.
• AI Format
• Footnote of each page www.spinefsw.example.org

```html
<!DOCTYPE html>
<html lang="en">
<head>
<meta charset="utf-8">
<title>FSW 2018 Desk Calendar – May</title>
<link href="https://fonts.googleapis.com/css2?family=Arvo:wght@700&family=Michroma&family=Orbitron:wght@700;800&family=Open+Sans:wght@400&display=swap" rel="stylesheet">
<style>
  :root {
    --paper: #f2efdf;
    --olive: #9c9a38;
    --olive-dark: #8d8b30;
    --lime: #e3df3a;
    --lime-pale: #f1ec7a;
    --sage: #d9d6a6;
    --ink: #1a1a1a;
    --sunday: #e0262b;
    --rule: #a7a357;
    --white: #ffffff;
  }
  html, body {
    margin: 0;
    padding: 0;
    overflow: hidden;
    background: var(--paper);
  }
  .calendar-page {
    position: relative;
    width: 1117px;
    height: 1200px;
    overflow: hidden;
    background: var(--paper);
    font-family: "Orbitron", "Michroma", sans-serif;
    color: var(--ink);
  }
  .backdrop {
    position: absolute;
    inset: 0;
    width: 1117px;
    height: 1200px;
  }
  .spine-fact {
    position: absolute;
    right: 344px;
    top: 28px;
    margin: 0;
    text-align: right;
    font-family: "Arvo", Georgia, serif;
    font-weight: 700;
    font-size: 30px;
    line-height: 39px;
    color: var(--white);
    text-shadow: 0 1px 3px rgba(120, 70, 10, 0.35);
  }
  .mini-month {
    position: absolute;
    left: 848px;
    top: 284px;
    width: 245px;
  }
  .mini-month h3 {
    margin: 0 0 6px 82px;
    font-family: "Michroma", sans-serif;
    font-weight: 400;
    font-size: 17px;
    letter-spacing: 1px;
  }
  .mini-grid {
    display: grid;
    grid-template-columns: repeat(7, 35px);
    grid-auto-rows: 29px;
    font-weight: 800;
    font-size: 14px;
  }
  .mini-grid span { padding-left: 6px; }
  .sun { color: var(--sunday); }
  .month-name {
    position: absolute;
    left: 784px;
    top: 508px;
    margin: 0;
    font-family: "Michroma", sans-serif;
    font-weight: 400;
    font-size: 66px;
    letter-spacing: 2px;
    color: var(--olive);
  }
  .anniversary-mark {
    position: absolute;
    left: 630px;
    top: 520px;
    display: flex;
    align-items: center;
    gap: 8px;
    font-family: "Arvo", Georgia, serif;
    font-weight: 700;
    font-size: 24px;
    color: #2b3a8c;
  }
  .anniversary-mark .dot {
    width: 34px;
    height: 34px;
    border-radius: 50%;
    background: var(--lime);
  }
  .month-grid {
    position: absolute;
    left: 142px;
    top: 612px;
    width: 910px;
  }
  .week {
    position: relative;
    height: 96px;
    border-bottom: 2px solid var(--rule);
    font-size: 31px;
    font-weight: 800;
  }
  .week.heading {
    height: 54px;
    border-bottom: none;
  }
  .week span {
    position: absolute;
    bottom: 6px;
  }
  .week.heading span { bottom: 12px; }
  .c1 { left: 8px; } .c2 { left: 127px; } .c3 { left: 259px; }
  .c4 { left: 389px; } .c5 { left: 520px; } .c6 { left: 648px; } .c7 { left: 777px; }
  .site-footer {
    position: absolute;
    right: 22px;
    top: 1160px;
    font-family: "Open Sans", Arial, sans-serif;
    font-size: 20px;
    color: var(--ink);
  }
</style>
</head>
<body>
<main class="calendar-page">
  <svg class="backdrop" viewBox="0 0 1117 1200" xmlns="http://www.w3.org/2000/svg">
    <defs>
      <linearGradient id="sunsetGlow" x1="0" y1="0.6" x2="1" y2="0.2">
        <stop offset="0" stop-color="#e9a63a"/>
        <stop offset="0.35" stop-color="#d8a466"/>
        <stop offset="0.7" stop-color="#c9b08a"/>
        <stop offset="1" stop-color="#a58f6c"/>
      </linearGradient>
    </defs>
    <path role="img" aria-label="Photo of a runner stretching, holding the sole of a shoe at sunset"
          fill="url(#sunsetGlow)"
          d="M0 0 H1117 V20 C900 150 700 270 430 390 C260 460 110 570 0 720 Z"/>
    <path class="band-sage" fill="none" stroke="var(--sage)" stroke-width="34"
          d="M-10 770 C120 610 290 500 470 420 C720 300 920 180 1130 70"/>
    <path class="band-lime" fill="none" stroke="var(--lime)" stroke-width="22"
          d="M-10 740 C120 590 280 480 460 405 C710 290 910 165 1130 50"/>
    <path class="band-pale" fill="none" stroke="var(--lime-pale)" stroke-width="8"
          d="M-10 790 C130 630 300 520 480 440 C730 320 930 200 1130 95"/>
    <g role="img" aria-label="Illustrated row of spine vertebrae following the curve">
      <path fill="none" stroke="var(--olive)" stroke-width="70" stroke-linecap="round"
            d="M40 650 C140 540 270 460 440 395 C690 290 900 160 1110 40"/>
    </g>
  </svg>

  <p class="spine-fact">Spine Fact:<br>The Spine is incredibly<br>flexible. If bent, it would<br>form 2/3 of a cicle.</p>

  <section class="mini-month" aria-label="April 2018">
    <h3>APRIL</h3>
    <div class="mini-grid">
      <span>M</span><span>T</span><span>W</span><span>T</span><span>F</span><span>S</span><span class="sun">S</span>
      <span>30</span><span></span><span></span><span></span><span></span><span></span><span class="sun">1</span>
      <span>2</span><span>3</span><span>4</span><span>5</span><span>6</span><span>7</span><span class="sun">8</span>
      <span>9</span><span>10</span><span>11</span><span>12</span><span>13</span><span>14</span><span class="sun">15</span>
      <span>16</span><span>17</span><span>18</span><span>19</span><span>20</span><span>21</span><span class="sun">22</span>
      <span>23</span><span>24</span><span>25</span><span>26</span><span>27</span><span>28</span><span class="sun">29</span>
    </div>
  </section>

  <div class="anniversary-mark"><span class="dot"></span>FSW</div>
  <h2 class="month-name">MAY</h2>

  <section class="month-grid" aria-label="May 2018">
    <div class="week heading">
      <span class="c1">M</span><span class="c2">T</span><span class="c3">W</span><span class="c4">T</span><span class="c5">F</span><span class="c6">S</span><span class="c7 sun">S</span>
    </div>
    <div class="week">
      <span class="c2">1</span><span class="c3">2</span><span class="c4">3</span><span class="c5">4</span><span class="c6">5</span><span class="c7 sun">6</span>
    </div>
    <div class="week">
      <span class="c1">7</span><span class="c2">8</span><span class="c3">9</span><span class="c4">10</span><span class="c5">11</span><span class="c6">12</span><span class="c7 sun">13</span>
    </div>
    <div class="week">
      <span class="c1">14</span><span class="c2">15</span><span class="c3">16</span><span class="c4">17</span><span class="c5">18</span><span class="c6">19</span><span class="c7 sun">20</span>
    </div>
    <div class="week">
      <span class="c1">21</span><span class="c2">22</span><span class="c3">23</span><span class="c4">24</span><span class="c5">25</span><span class="c6">26</span><span class="c7 sun">27</span>
    </div>
    <div class="week">
      <span class="c1">28</span><span class="c2">29</span><span class="c3">30</span><span class="c4">31</span>
    </div>
  </section>

  <footer class="site-footer">www.spinefsw.example.org</footer>
</main>
</body>
</html>
```